MRT Property - Business Cards

Looking for a business card & general letterhead, signage etc design for our new logo.

Colours:
000a20
0056a2
00b5ef
0088ce
68cef2

Fonts:
Poppins
Karla

Please keep look and feel of new brand - example in the zip package I sent.

```html
<!DOCTYPE html>
<html lang="en">
<head>
<meta charset="utf-8">
<title>MRT Property – Business Cards</title>
<link href="https://fonts.googleapis.com/css2?family=Montserrat:wght@400;500&family=Poppins:wght@700&family=Sue+Ellen+Francisco&display=swap" rel="stylesheet">
<style>
  :root {
    --navy: #000a20;
    --brand-blue: #0b56a4;
    --back-blue: #0b57a5;
    --back-mark: #1f4586;
    --ink: #1e1e1e;
    --icon-blue: #0088ce;
    --stage: #9a9a9a;
    --paper: #ffffff;
  }
  * { margin: 0; padding: 0; box-sizing: border-box; }
  html, body {
    width: 1093px;
    height: 1200px;
    overflow: hidden;
    background: var(--stage);
  }
  .card {
    position: absolute;
    left: 265px;
    width: 580px;
    height: 363px;
    border-radius: 16px;
    overflow: hidden;
  }
  .card--front { top: 225px; background: var(--paper); }
  .card--back { top: 617px; background: var(--back-blue); }

  .brand-name {
    position: absolute;
    font-family: "Poppins", sans-serif;
    font-weight: 700;
    white-space: nowrap;
  }
  .card--front .brand-name {
    left: 22px;
    top: 36px;
    font-size: 40px;
    line-height: 1;
    color: var(--brand-blue);
  }
  .card--back .brand-name {
    left: 0;
    right: 0;
    top: 150px;
    text-align: center;
    font-size: 62px;
    line-height: 1;
    color: var(--back-mark);
  }

  .holder {
    position: absolute;
    right: 35px;
    top: 28px;
    text-align: left;
  }
  .holder__name {
    font-family: "Sue Ellen Francisco", cursive;
    font-size: 30px;
    line-height: 1;
    color: var(--brand-blue);
  }
  .holder__title {
    font-family: "Montserrat", sans-serif;
    font-weight: 500;
    font-size: 13px;
    color: var(--ink);
    margin-top: 4px;
  }
  .holder-tab {
    position: absolute;
    right: 0;
    top: 26px;
    width: 20px;
    height: 47px;
    background: var(--brand-blue);
  }

  .address {
    position: absolute;
    left: 24px;
    top: 200px;
    font-family: "Montserrat", sans-serif;
    font-size: 14px;
    line-height: 16px;
    color: var(--ink);
  }
  .contacts {
    position: absolute;
    left: 25px;
    top: 266px;
    list-style: none;
    font-family: "Montserrat", sans-serif;
    font-size: 13.5px;
    color: var(--ink);
  }
  .contacts li {
    display: flex;
    align-items: center;
    height: 24.5px;
  }
  .contacts svg {
    width: 13px;
    height: 13px;
    margin-right: 10px;
    fill: var(--icon-blue);
  }
  .base-band {
    position: absolute;
    left: 0;
    right: 0;
    bottom: 0;
    height: 21px;
    background: var(--brand-blue);
  }
</style>
</head>
<body>
  <section class="card card--front">
    <div class="brand-name">MRT Property</div>

    <div class="holder">
      <div class="holder__name">Dana Whitfield</div>
      <div class="holder__title">Managing Director</div>
    </div>
    <div class="holder-tab"></div>

    <address class="address" style="font-style:normal">
      245 Cedar Bend Road<br>
      Ridgeland, MS 39157
    </address>

    <ul class="contacts">
      <li>
        <svg viewBox="0 0 24 24" aria-hidden="true"><path d="M6.6 10.8a15.1 15.1 0 0 0 6.6 6.6l2.2-2.2a1 1 0 0 1 1-.25 11.4 11.4 0 0 0 3.6.57 1 1 0 0 1 1 1V20a1 1 0 0 1-1 1A17 17 0 0 1 3 4a1 1 0 0 1 1-1h3.5a1 1 0 0 1 1 1c0 1.25.2 2.45.57 3.57a1 1 0 0 1-.25 1z"/></svg>
        555.214.3307
      </li>
      <li>
        <svg viewBox="0 0 24 24" aria-hidden="true"><path d="M2 5h20v2l-10 6L2 7zM2 9l10 6 10-6v10H2z"/></svg>
        info@mrtproperty.com
      </li>
      <li>
        <svg viewBox="0 0 24 24" aria-hidden="true"><path d="M12 2a10 10 0 1 0 0 20 10 10 0 0 0 0-20zm-1 17.9A8 8 0 0 1 4.1 11H8v2l3 3zm6.9-2.5A2 2 0 0 0 16 16h-1v-3a1 1 0 0 0-1-1H8v-2h2a1 1 0 0 0 1-1V7h2a2 2 0 0 0 2-2v-.4a8 8 0 0 1 2.9 12.8z"/></svg>
        www.mrtproperty.com
      </li>
    </ul>

    <div class="base-band"></div>
  </section>

  <section class="card card--back">
    <div class="brand-name">MRT Property</div>
  </section>
</body>
</html>
```